Exciting & Elegant Stationary Pack

Stationary consists of
1. Letter head / Envelope
2. Business Card
3. Invoice
4. 40x40mm sticker

Attached files;

1. Logo (Other formats available on request)
2. MS word Doc - For information and description of design
3. Website image (This will be our new website so use the colours so everything ties together)
4. Sample of stationary pack we like, but feel free to be creative

Target Market(s)

Home improvement

Industry/Entity Type

Construction

Font styles to use
Other font styles liked:
• Leave up to designer - We like font used on (website attached image)

Requirements
Must have
• Please look at uploaded file of sample website and use colours
Nice to have
• Any type of business card design - eg. metal, die cut, embossed, etc...

```html
<!DOCTYPE html>
<html lang="en">
<head>
<meta charset="utf-8">
<title>Grout &amp; Grain – Business Card</title>
<link rel="stylesheet" href="https://fonts.googleapis.com/css2?family=Open+Sans:wght@400;700&display=swap">
<style>
  :root {
    --backdrop: #7f8082;
    --card: #efefef;
    --navy: #1f3f66;
    --orange: #d9782d;
    --ink: #4a4a4a;
    --ink-strong: #333333;
  }
  * { box-sizing: border-box; margin: 0; padding: 0; }
  html, body {
    width: 1200px;
    height: 814px;
    overflow: hidden;
    background: var(--backdrop);
    font-family: "Open Sans", Verdana, sans-serif;
  }
  .sheet {
    width: 1200px;
    height: 814px;
    display: flex;
    align-items: center;
    justify-content: center;
    gap: 40px;
  }
  .card {
    position: relative;
    width: 520px;
    height: 318px;
    background: var(--card);
    box-shadow: 0 2px 6px rgba(0,0,0,0.18);
  }
  .card__frame {
    position: absolute;
    inset: 14px;
    border: 2px solid var(--navy);
  }
  .card__content {
    position: absolute;
    inset: 0;
    display: flex;
    flex-direction: column;
    align-items: center;
    justify-content: center;
    text-align: center;
  }
  .contact__name {
    color: var(--navy);
    font-weight: 700;
    font-size: 22px;
    letter-spacing: 0.5px;
    line-height: 1.2;
  }
  .contact__role {
    color: var(--orange);
    font-size: 17px;
    line-height: 1.3;
  }
  .contact__licence {
    color: var(--ink);
    font-size: 16px;
    line-height: 1.5;
  }
  .contact__phone {
    color: var(--ink-strong);
    font-weight: 700;
    font-size: 21px;
    letter-spacing: 1px;
    line-height: 1.4;
  }
  .contact__line {
    color: var(--ink);
    font-size: 16px;
    line-height: 1.4;
  }
  .brand {
    display: flex;
    align-items: center;
    gap: 12px;
  }
  .brand__mark {
    width: 26px;
    height: 26px;
    background: var(--navy);
  }
  .brand__name {
    color: var(--navy);
    font-weight: 700;
    font-size: 34px;
    letter-spacing: 1px;
  }
</style>
</head>
<body>
  <main class="sheet">
    <section class="card card--contact" aria-label="Business card back">
      <div class="card__frame"></div>
      <div class="card__content">
        <p class="contact__name">MINH TRAN</p>
        <p class="contact__role">Project Manager</p>
        <p class="contact__licence">Lic No. 204918c</p>
        <p class="contact__phone">0400 555 192</p>
        <p class="contact__line">hello@groutandgrain.com.au</p>
        <p class="contact__line">www.groutandgrain.com.au</p>
      </div>
    </section>

    <section class="card card--brand" aria-label="Business card front">
      <div class="card__frame"></div>
      <div class="card__content">
        <div class="brand">
          <span class="brand__mark"></span>
          <span class="brand__name">Grout &amp; Grain</span>
        </div>
      </div>
    </section>
  </main>
</body>
</html>
```